Brochure required

Looking at getting business brochure designed for my solar sales company. i will require a range of products to be listed on the brochure I require a simple/ elegent / professional looking brochure.

I am happy to provide designer with all the required information that must go into the brochure. otherwise please visit www.quillebartow.com.au and view the products which i would like to allocate into the brochure aswell as our company logo and a little about me section

```html
<!DOCTYPE html>
<html lang="en">
<head>
<meta charset="utf-8">
<title>Quillebartow Brochure</title>
<link rel="stylesheet" href="https://fonts.googleapis.com/css2?family=Montserrat:wght@500;600;700&family=Open+Sans:wght@400;600&display=swap">
<style>
:root{
  --backdrop:#e8e3e1;
  --paper:#ffffff;
  --teal:#1e8fb5;
  --green:#2cb58e;
  --green-dark:#1f9a78;
  --ink:#3a3a3a;
  --muted:#6b6b6b;
  --gold:#c9a82c;
  --blue-deep:#0f7fb0;
  --sky:#b9d3e8;
  --panel:#2d3d5c;
  --grass:#5c8a3a;
}
*{box-sizing:border-box;margin:0;padding:0}
html,body{width:768px;height:1200px;overflow:hidden;background:var(--backdrop)}
body{font-family:"Open Sans",Arial,sans-serif;color:var(--ink);position:relative}
.spread{position:absolute;left:44px;width:680px;height:481px;display:flex;box-shadow:0 6px 18px rgba(0,0,0,.12)}
.spread.cover{top:40px}
.spread.inner{top:580px}
.page{position:relative;width:340px;height:481px;background:var(--paper);overflow:hidden}
.page + .page{border-left:1px solid #e2e2e2}
.page svg.art{position:absolute;left:0;top:0}
.brand{display:flex;align-items:center;gap:6px;font-family:"Montserrat",sans-serif;font-weight:700;color:var(--ink)}
.brand .mark{width:14px;height:14px;background:var(--green)}
/* front cover */
.front .brand{position:absolute;left:52px;top:34px;font-size:18px}
.headline{position:absolute;left:52px;top:66px;font-family:"Montserrat",sans-serif;font-weight:600;line-height:1.05}
.headline .lead{display:block;color:var(--teal);font-size:24px}
.headline .tail{display:block;color:var(--ink);font-size:24px;padding-left:34px}
/* back cover */
.back .brand{position:absolute;left:150px;top:262px;font-size:15px}
.back .call{position:absolute;left:166px;top:284px;font-family:"Montserrat",sans-serif;font-weight:600;font-size:10px;color:var(--teal);letter-spacing:.5px}
.back .phone{position:absolute;left:150px;top:297px;font-family:"Montserrat",sans-serif;font-weight:500;font-size:21px;color:var(--ink)}
.contact{position:absolute;left:120px;width:200px;text-align:center;font-size:8.5px;color:var(--muted)}
.contact .icon{display:block;margin:0 auto 3px}
.contact.email{top:336px}
.contact.web{top:370px}
/* inner */
.inner p{font-size:6.6px;line-height:1.45;color:var(--muted)}
.inner h3{font-family:"Montserrat",sans-serif;font-weight:600;font-size:10px;color:var(--teal);text-transform:uppercase;margin-bottom:3px}
.intro{position:absolute;left:30px;top:26px;width:285px}
.product{position:absolute}
.product .shot{position:absolute}
.p1{left:118px;top:80px;width:190px}
.p1 .shot{left:-90px;top:2px;width:70px;height:66px;background:linear-gradient(135deg,#dfe3e7,#a9b1bb);border-radius:2px}
.p1 .more{position:absolute;left:-90px;top:88px;width:280px}
.p2{left:118px;top:180px;width:190px}
.p2 .shot{left:-90px;top:0;width:62px;height:62px;background:linear-gradient(135deg,#3b5a9a,#1d2e55)}
.p2 .more{position:absolute;left:-90px;top:62px;width:280px}
.p-right{left:22px;width:200px}
.p3{top:36px}
.p4{top:118px}
.inverter{position:absolute;width:62px;height:72px;border-radius:8px}
.inv1{left:248px;top:56px;background:linear-gradient(160deg,#f4f4f4,#cfcfcf);border-bottom:10px solid #d3242c}
.inv2{left:248px;top:140px;background:linear-gradient(160deg,#eeeeee,#a9a9a9);border-bottom:10px solid #555}
.ppa{position:absolute;left:22px;top:216px;width:296px}
.ppa p + p{margin-top:4px}
.chart{position:absolute;left:30px;top:322px}
.chart text{font-family:"Open Sans",sans-serif;font-size:6px;fill:var(--muted)}
</style>
</head>
<body>

<section class="spread cover">
  <article class="page back">
    <svg class="art" width="340" height="481" viewBox="0 0 340 481">
      <path d="M 150 20 A 118 118 0 0 1 150 250" fill="none" stroke="var(--gold)" stroke-width="6"/>
      <defs>
        <linearGradient id="installer" x1="0" y1="0" x2="0" y2="1">
          <stop offset="0" stop-color="#4b7fc4"/>
          <stop offset=".5" stop-color="#8fb1d8"/>
          <stop offset="1" stop-color="#2f3d5e"/>
        </linearGradient>
        <linearGradient id="wave" x1="0" y1="0" x2="1" y2="0">
          <stop offset="0" stop-color="var(--green)"/>
          <stop offset="1" stop-color="var(--blue-deep)"/>
        </linearGradient>
      </defs>
      <circle cx="62" cy="135" r="122" fill="url(#installer)" role="img" aria-label="Photo of an installer fitting a solar panel on a roof"/>
      <path d="M 0 481 L 0 455 C 60 405 180 392 340 398 L 340 481 Z" fill="url(#wave)"/>
    </svg>
    <div class="brand"><span class="mark"></span>Quillebartow</div>
    <div class="call">CALL US NOW</div>
    <div class="phone">0400 318 552</div>
    <div class="contact email">
      <svg class="icon" width="12" height="12" viewBox="0 0 12 12"><circle cx="6" cy="6" r="5.5" fill="var(--teal)"/><rect x="3" y="4" width="6" height="4" fill="#fff"/><path d="M3 4 L6 6.4 L9 4" stroke="var(--teal)" stroke-width=".7" fill="none"/></svg>
      hello@quillebartow.com.au
    </div>
    <div class="contact web">
      <svg class="icon" width="12" height="12" viewBox="0 0 12 12"><circle cx="6" cy="6" r="5.5" fill="var(--teal)"/><circle cx="6" cy="6" r="3" fill="none" stroke="#fff" stroke-width=".8"/><line x1="3" y1="6" x2="9" y2="6" stroke="#fff" stroke-width=".7"/></svg>
      www.quillebartow.com.au
    </div>
  </article>

  <article class="page front">
    <div class="brand"><span class="mark"></span>Quillebartow</div>
    <h1 class="headline"><span class="lead">Energy solutions for a</span><span class="tail">changing world</span></h1>
    <svg class="art" width="340" height="481" viewBox="0 0 340 481">
      <defs>
        <linearGradient id="field" x1="0" y1="0" x2="0" y2="1">
          <stop offset="0" stop-color="var(--sky)"/>
          <stop offset=".35" stop-color="#f3e6c6"/>
          <stop offset=".55" stop-color="var(--panel)"/>
          <stop offset="1" stop-color="var(--grass)"/>
        </linearGradient>
      </defs>
      <path d="M 110 230 C 170 200 290 196 340 212 L 340 481 L 150 481 C 100 420 90 310 110 230 Z" fill="var(--green)"/>
      <ellipse cx="250" cy="380" rx="148" ry="122" fill="#fff"/>
      <ellipse cx="252" cy="382" rx="143" ry="117" fill="url(#field)" role="img" aria-label="Photo of a solar panel array in a field at sunrise"/>
    </svg>
  </article>
</section>

<section class="spread inner">
  <article class="page">
    <p class="intro">We partner with trusted panel makers to bring you reliable, efficient solar for homes and businesses. Every product we supply is tested, warranted and chosen for long life in local conditions.</p>

    <div class="product p1">
      <div class="shot" role="img" aria-label="Product photo of the Solvane 270W panel"></div>
      <h3>Solvane 270W</h3>
      <p>A proven double certified module built for the highest reliability in all conditions.</p>
      <p>The Solvane series is tested well beyond industry standards, giving strong output even in low light and high heat.</p>
      <p class="more">This panel sets a new standard for reliability and performance, with power classes up to 275W.</p>
    </div>

    <div class="product p2">
      <div class="shot" role="img" aria-label="Product photo of the Solvane Kestrel PERC panel"></div>
      <h3>Solvane Kestrel PERC 60M 300W</h3>
      <p>A highly efficient monocrystalline panel from a tier one maker at an affordable price.</p>
      <p>Its sleek black finish suits any roof while lifting output.</p>
      <p class="more">The Halden five busbar cell design improves efficiency while keeping a clean look.</p>
    </div>

    <svg class="art" width="340" height="481" viewBox="0 0 340 481">
      <defs>
        <linearGradient id="rows" x1="0" y1="0" x2="0" y2="1">
          <stop offset="0" stop-color="var(--sky)"/>
          <stop offset=".4" stop-color="var(--panel)"/>
          <stop offset="1" stop-color="var(--grass)"/>
        </linearGradient>
      </defs>
      <path d="M 0 300 C 110 290 250 330 340 420" fill="none" stroke="var(--green)" stroke-width="5"/>
      <path d="M 0 310 C 110 300 250 340 340 430 L 340 481 L 0 481 Z" fill="url(#rows)" role="img" aria-label="Photo of rows of solar panels in a field"/>
    </svg>
  </article>

  <article class="page">
    <div class="product p-right p3">
      <h3>Verant Hybrid</h3>
      <p>The Axis Hybrid is one of the first high voltage hybrid inverters on the market.</p>
      <p>It lets homes store solar power in a battery and use it at night, with smart monitoring, Wi-Fi and an extendable warranty.</p>
    </div>
    <div class="inverter inv1" role="img" aria-label="Product photo of the Verant Hybrid inverter"></div>

    <div class="product p-right p4">
      <h3>Verant Axis 5.0-1 Inverter</h3>
      <p>A great choice for larger homes or small commercial sites on a single phase connection.</p>
      <p>The Axis is among the latest additions to the range, with high efficiency, Wi-Fi monitoring and models from 3kW to 8kW.</p>
    </div>
    <div class="inverter inv2" role="img" aria-label="Product photo of the Verant Axis inverter"></div>

    <div class="ppa">
      <h3>PPA's</h3>
      <p>A Power Purchase Agreement gets you on the path to energy independence with no upfront costs.</p>
      <p>A PPA is a fixed term plan where you pay a fixed c/kWh rate.</p>
      <p>Typically, the fixed rate is lower than your current retailer charge and protects you from rises during the term.</p>
    </div>

    <svg class="chart" width="280" height="120" viewBox="0 0 280 120">
      <line x1="20" y1="8" x2="20" y2="104" stroke="#999" stroke-width=".8"/>
      <line x1="20" y1="104" x2="272" y2="104" stroke="var(--green-dark)" stroke-width="1"/>
      <g fill="#eef1f3" stroke="#cfd6db" stroke-width=".5">
        <rect x="80" y="36" width="190" height="68"/>
      </g>
      <g stroke="#d9dfe3" stroke-width=".5">
        <line x1="95" y1="36" x2="95" y2="104"/><line x1="110" y1="38" x2="110" y2="104"/>
        <line x1="125" y1="40" x2="125" y2="104"/><line x1="140" y1="43" x2="140" y2="104"/>
        <line x1="155" y1="46" x2="155" y2="104"/><line x1="170" y1="50" x2="170" y2="104"/>
        <line x1="185" y1="54" x2="185" y2="104"/><line x1="200" y1="58" x2="200" y2="104"/>
        <line x1="215" y1="63" x2="215" y2="104"/><line x1="230" y1="68" x2="230" y2="104"/>
        <line x1="245" y1="74" x2="245" y2="104"/><line x1="260" y1="80" x2="260" y2="104"/>
      </g>
      <rect x="36" y="60" width="40" height="32" fill="var(--panel)" role="img" aria-label="Small solar panel illustration"/>
      <path d="M 20 30 L 80 30 C 150 34 220 60 272 88" fill="none" stroke="#333" stroke-width="1"/>
      <path d="M 20 58 L 272 58" fill="none" stroke="var(--green)" stroke-width="1"/>
      <text x="24" y="25">Retailer rate</text>
      <text x="24" y="54">PPA rate</text>
      <text x="252" y="114">Time</text>
    </svg>
  </article>
</section>

</body>
</html>
```